Tech business card design

We need an amazing business card design for our new business 'Pexla' a marketing tech startup based in Sydney, Australia. We provide an online marketplace for businesses to search and buy advertising media, connect with service providers and learn more about marketing. We wish to communicate 'cool tech', reliability and professionalism and design based around our logo.

Target Market(s)

Business Owners

Contact Information for Business Card

Name
Position
Email Address
Website
Phone Number

Font styles to use
Other font styles liked:
• Avenir & Avenir Next

Colors

Designer to choose colors to be used in the design.

```html
<!DOCTYPE html>
<html lang="en">
<head>
<meta charset="utf-8">
<title>Pexla Business Card</title>
<link rel="stylesheet" href="https://fonts.googleapis.com/css2?family=Nunito+Sans:wght@400;600;800&display=swap">
<style>
  :root {
    --stage: #f1f1f1;
    --navy: #141a3d;
    --navy-deep: #0d1230;
    --navy-soft: #1c2350;
    --paper: #ffffff;
    --line-grey: #e6e7ea;
    --ink-soft: #c9cbd6;
    --text-dark: #1b1f33;
  }
  * { box-sizing: border-box; margin: 0; padding: 0; }
  html, body {
    width: 1200px; height: 800px; overflow: hidden;
    background: var(--stage);
    font-family: "Nunito Sans", Arial, sans-serif;
  }
  .stage { position: relative; width: 1200px; height: 800px; }
  .card {
    position: absolute; top: 268px;
    width: 460px; height: 263px;
    overflow: hidden;
    box-shadow: 0 2px 6px rgba(0,0,0,0.12);
  }
  /* Back face */
  .card-back { left: 90px; background: var(--paper); }
  .icon-pattern {
    position: absolute; inset: 0;
    background: linear-gradient(135deg, #fbfbfb 0%, var(--line-grey) 100%);
    opacity: 0.7;
  }
  .brand-disc {
    position: absolute; left: 148px; top: 49px;
    width: 164px; height: 164px; border-radius: 50%;
    background: var(--navy);
    display: flex; align-items: center; justify-content: center;
  }
  .brand-disc .wordmark { font-size: 44px; }
  .back-url {
    position: absolute; right: 18px; bottom: 14px;
    font-size: 11px; color: var(--text-dark); letter-spacing: 0.2px;
  }
  .wordmark {
    color: var(--paper); font-weight: 800; letter-spacing: -0.5px; line-height: 1;
  }
  /* Front face */
  .card-front { left: 650px; background: var(--navy); }
  .logo-pattern {
    position: absolute; inset: 0;
    background: linear-gradient(180deg, var(--navy-soft) 0%, var(--navy) 100%);
  }
  .name-block {
    position: absolute; left: 0; top: 0;
    width: 168px; height: 56px;
    background: var(--navy-deep);
    padding: 13px 0 0 14px;
  }
  .person-name {
    color: var(--paper); font-size: 14.5px; font-weight: 600; letter-spacing: 0.4px; line-height: 1;
  }
  .person-role {
    color: var(--ink-soft); font-size: 9.5px; margin-top: 5px;
  }
  .front-wordmark {
    position: absolute; left: 0; right: 0; top: 103px;
    text-align: center; font-size: 28px;
  }
  .contact-list {
    position: absolute; left: 296px; top: 188px;
    list-style: none;
  }
  .contact-list li {
    display: flex; align-items: center; gap: 9px;
    color: var(--paper); font-size: 10px; line-height: 14px; height: 14px;
    white-space: nowrap;
  }
  .contact-list span { color: var(--paper); text-decoration: none; }
  .contact-list svg { width: 9px; height: 9px; fill: var(--paper); flex: none; }
</style>
</head>
<body>
<main class="stage">
  <section class="card card-back" aria-label="Card back">
    <div class="icon-pattern" role="img" aria-label="Faint line-icon pattern of marketing symbols"></div>
    <div class="brand-disc"><span class="wordmark">pexla</span></div>
    <p class="back-url">www.pexlamail.com</p>
  </section>

  <section class="card card-front" aria-label="Card front">
    <div class="logo-pattern" role="img" aria-label="Tone-on-tone repeated brand name pattern"></div>
    <div class="name-block">
      <p class="person-name">DANIEL MARSH</p>
      <p class="person-role">Managing Director</p>
    </div>
    <p class="wordmark front-wordmark">pexla</p>
    <ul class="contact-list">
      <li>
        <svg viewBox="0 0 10 10" aria-hidden="true"><path d="M1 3.5 Q5 0.5 9 3.5 L8 4.8 L6.6 4 L6.6 3 Q5 2.4 3.4 3 L3.4 4 L2 4.8 Z M2.5 5.5 H7.5 L8.5 9 H1.5 Z"/></svg>
        <span>000-555-0192</span>
      </li>
      <li>
        <svg viewBox="0 0 10 10" aria-hidden="true"><path d="M0.5 2 H9.5 V8.5 H0.5 Z M1 2.5 L5 5.6 L9 2.5" fill="none" stroke="#fff" stroke-width="1"/></svg>
        <span>info@pexlamail.com</span>
      </li>
      <li>
        <svg viewBox="0 0 10 10" aria-hidden="true"><g fill="none" stroke="#fff" stroke-width="0.9"><circle cx="5" cy="5" r="4.3"/><ellipse cx="5" cy="5" rx="1.9" ry="4.3"/><path d="M0.7 5 H9.3 M1.5 2.8 H8.5 M1.5 7.2 H8.5"/></g></svg>
        <span>www.pexlamail.com</span>
      </li>
    </ul>
  </section>
</main>
</body>
</html>
```